Young Architect Bussiness Card

English is not my first language (spanish is).
Need a bussiness card design for my best friend who is about to graduate from college, Licentiate degree in architecture, so she needs business cards to start networking, currently she has no porfolio, web page or plazared. so she is relying on her cel phone and correovela, but should leave space for one of them (plazared)

Design for business card should be modern, maybe something with construction blue prints patern or 3D modelling.

Name: Mariela Otárola Bonilla
Licentiate in Arquitecture
Cel: (506) XXX-4827
email: marielaXXX@correovela.com

Services, although im not sure if it has to be there or not:
Anteproyectos / Proposal design
Inspecciones / Site Inspections
Modelado 3D / 3D modelling
Planos Constructivos / Construction Blue Prints
Presupuestos / Budgets

Design should be in spanish

Industry/Entity Type

Architect

Contact Information for Business Card

Name: Mariela Otárola, Arquitecto
Associtation code : XXXX
Phone: (506) XXXX-XXXX
Email: xxx@correovela.com
Plazared: xxxx

Requirements
Must have
• Design for business card should be modern, maybe something with construction blue prints patern or 3D modelling.
Nice to have
• Something like a transition from 2D to 3D.

```html
<!DOCTYPE html>
<html lang="es">
<head>
<meta charset="utf-8">
<title>Tarjeta de presentación — Mariela Otárola Bonilla</title>
<link rel="stylesheet" href="https://fonts.googleapis.com/css2?family=Lato:wght@400;700&display=swap">
<style>
  :root {
    --canvas-bg: #2a2a2c;
    --card-white: #ffffff;
    --brand-blue: #1d7fd0;
    --cube-dark: #0d4fa6;
    --cube-mid: #2f7fdc;
    --cube-light: #5aa2e8;
    --cube-violet: #5a4fb8;
    --ink: #2b2b2b;
    --on-blue: #ffffff;
  }
  * { box-sizing: border-box; margin: 0; padding: 0; }
  html, body { width: 1200px; height: 880px; overflow: hidden; }
  body {
    background: var(--canvas-bg);
    font-family: "Lato", sans-serif;
    display: flex;
    flex-direction: column;
    align-items: center;
    justify-content: center;
    gap: 24px;
  }
  .card {
    position: relative;
    width: 720px;
    height: 400px;
    border-radius: 22px;
    overflow: hidden;
  }
  .card--front { background: var(--card-white); }
  .card--back { background: var(--brand-blue); }

  .cube-art {
    position: absolute;
    top: 0;
    right: 0;
    height: 100%;
  }
  .card--front .cube-art {
    width: 40%;
    background: linear-gradient(160deg, var(--cube-light) 0%, var(--cube-mid) 35%, var(--cube-dark) 60%, var(--cube-mid) 85%);
    clip-path: polygon(30% 0, 100% 0, 100% 78%, 60% 100%, 22% 100%, 0 62%, 12% 30%);
  }
  .card--back .cube-art {
    width: 48%;
    height: 78%;
    background: linear-gradient(160deg, rgba(90,162,232,0.6) 0%, var(--cube-mid) 35%, var(--cube-dark) 60%, rgba(47,127,220,0.5) 90%);
    clip-path: polygon(20% 10%, 85% 0, 100% 20%, 100% 70%, 65% 100%, 28% 90%, 4% 45%);
  }

  .identity {
    position: absolute;
    left: 48px;
    top: 62px;
  }
  .identity__name {
    color: var(--brand-blue);
    font-weight: 700;
    font-size: 23px;
    letter-spacing: 0.3px;
    text-transform: uppercase;
  }
  .identity__title {
    color: var(--ink);
    font-size: 18px;
    margin-top: 2px;
  }

  .contact {
    position: absolute;
    left: 48px;
    bottom: 52px;
    list-style: none;
    font-size: 19px;
    line-height: 1.3;
  }
  .contact__label { color: var(--brand-blue); font-weight: 700; }
  .contact__value { color: var(--ink); }

  .services {
    position: absolute;
    left: 48px;
    bottom: 46px;
    color: var(--on-blue);
  }
  .services__heading {
    font-size: 20px;
    font-weight: 700;
    letter-spacing: 0.5px;
    margin-bottom: 14px;
  }
  .services__list {
    list-style: none;
    font-size: 19px;
    line-height: 1.3;
    padding-left: 18px;
  }
</style>
</head>
<body>
  <section class="card card--front" aria-label="Frente de la tarjeta">
    <div class="cube-art" role="img" aria-label="Ilustración de cubos azules 3D que se dispersan"></div>
    <header class="identity">
      <h1 class="identity__name">Mariela Otárola Bonilla</h1>
      <p class="identity__title">Licentiate in Arquitecture</p>
    </header>
    <ul class="contact">
      <li><span class="contact__label">Associtation code :</span> <span class="contact__value">XXXX</span></li>
      <li><span class="contact__label">Cell:</span> <span class="contact__value">(506) XXX-4827</span></li>
      <li><span class="contact__label">Email:</span> <span class="contact__value">marielaXXX@correovela.com</span></li>
      <li><span class="contact__label">Plazared:</span> <span class="contact__value">xxxx</span></li>
    </ul>
  </section>

  <section class="card card--back" aria-label="Reverso de la tarjeta">
    <div class="cube-art" role="img" aria-label="Ilustración de cubos azules 3D que se dispersan"></div>
    <div class="services">
      <h2 class="services__heading">SERVICES</h2>
      <ul class="services__list">
        <li>Anteproyectos / Proposal design</li>
        <li>Inspecciones / Site Inspections</li>
        <li>Modelado 3D / 3D modelling</li>
        <li>Planos Constructivos / Construction Blue Prints</li>
        <li>Presupuestos / Budgets</li>
      </ul>
    </div>
  </section>
</body>
</html>
```